Vision, Mission and Culture Posters

We have written text paragraphs for our company vision and mission and need them made into a2 or a3 sized posters using our logo for inspiration for colour. Our company culture has 10 paragraphs and we'd like this to be a single poster of a2 or a1. Each poster should have the logo on and share common design. It's not a complex job really.

Industry/Entity Type

It Company

Requirements
Nice to have
• These will be going up on our office wall so need to be clear to read from a distance and look professional but also not stodgy.

```html
<!DOCTYPE html>
<html lang="en">
<head>
<meta charset="utf-8">
<title>Kerbside Bay Hire – Mission</title>
<link rel="stylesheet" href="https://fonts.googleapis.com/css2?family=Anton&family=Alfa+Slab+One&family=Archivo+Black&family=Rubik:wght@700;900&family=Roboto+Condensed:wght@400&family=Zilla+Slab:wght@500&display=swap">
<style>
  :root {
    --yellow: #fff200;
    --red: #d2232a;
    --ink: #0b0b0b;
    --paper: #f6f6f3;
    --paper-edge: #efe6b4;
    --white: #ffffff;
  }
  * { margin: 0; padding: 0; box-sizing: border-box; }
  html, body { width: 1200px; height: 849px; overflow: hidden; }
  body {
    position: relative;
    background: radial-gradient(ellipse 70% 75% at 50% 50%, var(--paper) 55%, var(--paper-edge) 100%);
    font-family: "Roboto Condensed", Arial, sans-serif;
  }
  .bands { position: absolute; inset: 0; width: 1200px; height: 849px; }

  .brand {
    position: absolute; left: 105px; top: 28px; width: 368px; height: 109px;
    background: var(--yellow);
    border: 4px solid var(--ink); border-radius: 14px;
    display: flex; align-items: center; gap: 22px; padding-left: 26px;
  }
  .brand-mark { width: 62px; height: 62px; background: var(--red); flex: none; }
  .brand-name {
    font-family: "Rubik", Arial, sans-serif; font-weight: 700;
    font-size: 27px; line-height: 1.15; color: var(--ink); letter-spacing: 1px;
  }

  .poster-title {
    position: absolute; left: 540px; top: 28px; width: 388px; height: 110px;
    background: var(--ink); border-radius: 12px;
    display: flex; align-items: center; justify-content: center;
    font-family: "Anton", Impact, sans-serif; color: var(--yellow);
    font-size: 108px; line-height: 1; letter-spacing: 3px; padding-top: 4px;
  }

  .headline { position: absolute; left: 0; top: 180px; width: 1200px; height: 320px; }
  .headline-intro { font-family: "Zilla Slab", Georgia, serif; font-weight: 500; }
  .headline-verb { font-family: "Anton", Impact, sans-serif; }
  .headline-key { font-family: "Alfa Slab One", Georgia, serif; }
  .headline-goal { font-family: "Archivo Black", Arial, sans-serif; }

  .statement {
    position: absolute; left: 97px; top: 507px; width: 1006px; height: 298px;
    background: var(--ink); border-radius: 14px;
    outline: 3px solid var(--ink); outline-offset: 0;
    box-shadow: inset 0 0 0 5px var(--ink), inset 0 0 0 7px var(--white);
    text-align: center; padding: 26px 20px 0;
  }
  .statement-lead {
    font-family: "Rubik", Arial, sans-serif; font-weight: 900;
    color: var(--yellow); font-size: 29px; line-height: 43px; letter-spacing: -0.2px;
  }
  .statement-body {
    margin-top: 12px; color: var(--white);
    font-size: 25px; line-height: 36px;
  }
</style>
</head>
<body>
  <svg class="bands" viewBox="0 0 1200 849" aria-hidden="true">
    <path d="M0 0 H1200 V68 C1130 95 1095 165 1040 168 L0 153 Z" fill="var(--yellow)"/>
    <path d="M0 153 L1040 168 C1095 165 1130 95 1200 68" fill="none" stroke="var(--ink)" stroke-width="3"/>
    <path d="M0 829 L1150 810 C1175 810 1190 812 1200 815 V849 H0 Z" fill="var(--red)"/>
    <path d="M0 829 L1150 810 C1175 810 1190 812 1200 815" fill="none" stroke="var(--ink)" stroke-width="3"/>
  </svg>

  <div class="brand">
    <span class="brand-mark"></span>
    <span class="brand-name">Kerbside Bay<br>Hire</span>
  </div>

  <div class="poster-title">MISSION</div>

  <svg class="headline" viewBox="0 180 1200 320" role="heading" aria-level="1" aria-label="Our mission is to achieve great customer satisfaction">
    <text class="headline-intro" x="165" y="266" font-size="94" textLength="859" lengthAdjust="spacingAndGlyphs"
          fill="none" stroke="var(--ink)" stroke-width="1.6">OUR MISSION IS TO</text>
    <text class="headline-verb" transform="translate(233 487) rotate(-90)" font-size="86" textLength="209"
          lengthAdjust="spacingAndGlyphs" fill="var(--ink)">ACHIEVE</text>
    <text class="headline-key" x="250" y="370" font-size="104" textLength="780" lengthAdjust="spacingAndGlyphs"
          fill="var(--yellow)" stroke="var(--ink)" stroke-width="3" paint-order="stroke">GREAT CUSTOMER</text>
    <text class="headline-goal" x="250" y="487" font-size="132" textLength="779" lengthAdjust="spacingAndGlyphs"
          fill="var(--red)">SATISFACTION</text>
  </svg>

  <section class="statement">
    <p class="statement-lead">We believe our path to achieving this comes through giving a simple yet thorough and friendly service to our customers without unnecessary complication.</p>
    <p class="statement-body">We will achieve this through using the technology available to us, continual staff training and development, regular refinement of our practices and processes along with commitment to our roles and the foundations for building our success.</p>
  </section>
</body>
</html>
```